SitePress Direct-Booking Website for Bend, Oregon Vacation Rental — $750 Budget
Project Overview

We are looking for a talented SitePress designer/developer to create a clean, professional and inviting direct-booking website for Birch Lantern Retreat, an established short-term vacation rental in Bend, Oregon.

The property is currently successfully listed on Staynest and Hoplo. Our Staynest property has approximately a 4.98-star rating with more than 200 reviews, is an Staynest Visitor Pick, and ranks among the Top 1% of eligible homes.

Project Budget: $750

We will select the designer based on the quality of the initial concept, understanding of the property, proposed booking solution and ability to deliver a completed and functioning SitePress website.

Existing Staynest Listing

Please use our current Staynest listing as the primary reference for photographs, property details, amenities and design inspiration:

https://www.staynest-example.net/rooms/48172036

Original high-resolution photographs and additional property information will be provided to the selected designer.

Design Direction

We want the website to feel:

Upscale but comfortable
Warm and welcoming
Clean and uncluttered
Pacific Northwest / Central Oregon
Professional rather than corporate
Highly visual with large property photographs
Easy to navigate
Excellent on phones, tablets and desktop computers

We welcome creativity and want designers to show us their vision for the property rather than simply copying our Staynest listing.

The website should immediately communicate that Birch Lantern Retreat is a highly rated vacation rental in an excellent Bend location.

Key Property Features
3 bedrooms
2 bathrooms
Sleeps up to 6 guests
Pet friendly
Approximately a 5-minute walk to Bend's Tannery Row Quarter
Near restaurants, shopping and Larkspur Fields Pavilion
Private fenced backyard
Covered outdoor area
Off-street driveway parking
Fireplace
Well-equipped kitchen
Staynest Prime Keeper
Staynest Visitor Pick
Top 1% of eligible Staynest homes
Approximately 4.98 stars with 200+ guest reviews

Our location, guest reviews, cleanliness, comfort, backyard, pet-friendly accommodations and walkability should be major selling points throughout the website.

Website Structure

We anticipate approximately 6–7 pages:

Home

Large hero photograph with a strong opening message and prominent BOOK DIRECT and CHECK AVAILABILITY buttons.

The home page should quickly communicate:

BIRCH LANTERN RETREAT — BEND, OREGON

3 Bedrooms | 2 Baths | Sleeps 6 | Pet Friendly | Walk to Tannery Row

Our exceptional guest rating and Staynest history should also be prominently featured.

The House

Bedrooms, bathrooms, kitchen, living areas, backyard and major amenities.

Photo Gallery

Large, attractive and fast-loading photographs with an easy-to-use mobile gallery.

Location / Explore Bend

Tannery Row Quarter, Larkspur Fields Pavilion, Deschutes River, restaurants, breweries, shopping, downtown Bend and nearby outdoor recreation.

Guest Reviews

Selected guest reviews and prominent presentation of our strong Staynest reputation.

Availability & Book Direct

A simple and professional direct-booking experience.

Contact / FAQ

Contact information plus common questions regarding pets, parking, check-in/check-out, cancellations and other policies.

IMPORTANT — Direct Booking & Credit Card Requirements

We want guests to be able to book directly through the website without having to contact us first.

The website should use a proven SitePress vacation-rental booking plugin or system rather than a custom-built reservation/payment system.

Guests should be able to:

Select arrival and departure dates
See available dates
Enter number of guests
See nightly charges
See cleaning fees
See applicable lodging taxes and other charges
See the complete reservation total before paying
Enter guest/contact information
Pay securely by credit or debit card
Receive an automatic reservation confirmation

Paywell is our preferred credit-card processor.

Credit-card information must be processed securely through Paywell or another established payment processor. Credit-card information should NOT be stored directly on our SitePress website.

Staynest & Hoplo Calendar Synchronization

This is very important.

The direct-booking calendar must synchronize with our existing Staynest and Hoplo calendars to reduce the possibility of double bookings.

For this single-property website, we prefer a simple solution using Staynest/Hoplo calendar or iCal synchronization rather than an expensive monthly channel-management service, if practical.

The designer should clearly identify the booking plugin/system they propose using.

IMPORTANT — Tell Us Your Proposed Booking Solution

As part of your submission, please tell us:

Which SitePress booking plugin/system you recommend.
Whether it synchronizes availability with Staynest and Hoplo.
Whether it integrates directly with Paywell.
The initial cost of the plugin/software.
Any annual or monthly fees.
Whether any additional paid software or services will be required.

We strongly prefer a solution with little or no ongoing monthly software expense.

We do not want to select a designer and later discover that the proposed booking system requires an expensive monthly subscription.

SitePress & Technical Requirements

The completed project should include:

Fully functioning SitePress website
Responsive desktop/tablet/mobile design
Fast-loading pages
Optimized photographs
SSL/HTTPS compatibility
Direct-booking functionality
Paywell payment integration
Staynest calendar synchronization
Hoplo calendar synchronization
Automatic booking confirmations
Cleaning fee and lodging-tax calculations
Contact form
Vizor Maps/location integration
Basic spam/security protection
Vizor Metrics capability
Basic SEO setup
Search-engine submission capability
Easy owner editing of text, rates and photographs
Search Engine Optimization

The website should be structured for Vizor and other search engines.

Important search themes include:

Bend Oregon vacation rental
Bend Oregon vacation home
Tannery Row Quarter vacation rental
Vacation rental near Tannery Row Bend
Bend Oregon pet-friendly vacation rental
Bend vacation rental near Larkspur Fields Pavilion
Bend Oregon direct booking vacation rental

We are not expecting an extensive ongoing SEO campaign for the $750 project. We do expect proper page titles, descriptions, headings, image optimization and a good technical foundation for future SEO.

Ownership

Upon completion and final payment:

We own the completed SitePress website.
We receive full SitePress administrator access.
We control the domain and hosting accounts.
We own all custom design files created for the project.
All necessary login credentials are provided to us.
The website can be moved to another SitePress hosting provider in the future.
There should be no proprietary dependency on the developer after completion.
What We Want From Contestants

Please review our Staynest listing before submitting your concept.

We are particularly interested in seeing an initial homepage concept showing how you would present:

Birch Lantern Retreat
The Bend / Tannery Row location
Our photography
Our exceptional guest reviews and ratings
The Book Direct message
The availability/booking call-to-action

We will provide feedback on the concepts we like and work with the selected designer to refine and complete the website.

Our Goal

Our objective is straightforward:

Create a beautiful, trustworthy and easy-to-use website that encourages guests to book Birch Lantern Retreat directly with us.

The website will complement—not replace—our existing Staynest and Hoplo listings.

We want repeat guests and new customers to have an easy way to find the property, check availability and book directly while receiving the same professional experience they expect from a major vacation-rental platform.

Target Market(s)

Consumers looking to to travel to Mexico for vacation. Family or couples

Industry/Entity Type

Short term vacation rental industry

Coding

Coded - Design and coding required

Number of Pages Required

5+ page

Requirements
Must have
• Capabilities to accept credit card payments and link to other rental property sites calendars such as HOPLO and Staynset
Nice to have
• Option for best plugins for property rental

```html
<!DOCTYPE html>
<html lang="en">
<head>
<meta charset="utf-8">
<title>Birch Lantern Retreat — Bend, Oregon Vacation Rental</title>
<link rel="stylesheet" href="https://fonts.googleapis.com/css2?family=Fraunces:ital,opsz,wght@0,9..144,400;0,9..144,500;0,9..144,600;1,9..144,600&family=Inter:wght@400;500;600;700&display=swap">
<style>
:root{
  --rust:#b65a30;
  --rust-dark:#9c4a25;
  --ink:#2b2620;
  --muted:#6e655b;
  --cream:#fbf8f3;
  --sand:#f3ece1;
  --line:#e3d9ca;
  --forest:#33432f;
  --forest-deep:#2b3a28;
  --on-dark:#f4efe6;
  --gold:#c98a2e;
}
*{box-sizing:border-box;margin:0;padding:0}
html,body{width:1200px;height:4184px;overflow:hidden}
body{font-family:"Inter",sans-serif;color:var(--ink);background:var(--cream);font-size:13px;line-height:1.6}
.serif{font-family:"Fraunces",serif}
.wrap{width:964px;margin:0 auto;position:relative}
.eyebrow{font-size:10px;letter-spacing:.22em;text-transform:uppercase;color:var(--rust);font-weight:600}
h2.section-title{font-family:"Fraunces",serif;font-weight:500;font-size:36px;line-height:1.1;margin-top:14px;color:var(--ink)}
.btn{display:inline-flex;align-items:center;gap:10px;height:42px;padding:0 22px;border-radius:21px;font-size:11px;font-weight:700;letter-spacing:.08em;text-transform:uppercase;text-decoration:none}
.btn-rust{background:var(--rust);color:#fff}
.btn-ghost{border:1.5px solid rgba(255,255,255,.7);color:#fff}
.link-arrow{color:var(--rust);font-size:11.5px;font-weight:600;text-decoration:none}
.photo{border-radius:12px;position:relative;overflow:hidden}

/* HERO */
.hero{height:586px;position:relative;color:#fff}
.hero-photo{position:absolute;inset:0;background:linear-gradient(100deg,#4a3c31 0%,#6c5a4b 40%,#8b7a69 70%,#a39687 100%)}
.hero-photo::after{content:"";position:absolute;inset:0;background:linear-gradient(90deg,rgba(30,22,16,.72) 0%,rgba(30,22,16,.35) 60%,rgba(30,22,16,.2) 100%)}
.nav{position:relative;height:58px;display:flex;align-items:center;justify-content:space-between}
.brand{font-family:"Fraunces",serif;font-size:15px;font-weight:600;line-height:1.1}
.brand small{display:block;font-family:"Inter",sans-serif;font-size:7.5px;letter-spacing:.3em;font-weight:500;opacity:.8;margin-top:3px}
.nav-links{display:flex;gap:18px;font-size:11px;font-weight:500;margin-left:100px}
.nav-right{display:flex;align-items:center;gap:14px;font-size:11px}
.nav-right .btn{height:30px;padding:0 16px;font-size:9px}
.hero-content{position:relative;padding-top:68px}
.pill{display:inline-flex;align-items:center;gap:7px;background:rgba(255,255,255,.14);border-radius:14px;padding:5px 12px;font-size:8.5px;letter-spacing:.2em;font-weight:600}
.hero h1{font-family:"Fraunces",serif;font-weight:500;font-size:56px;line-height:1.05;margin-top:14px}
.hero .tagline{font-family:"Fraunces",serif;font-size:28px;font-weight:400;margin-top:6px;opacity:.92}
.stats{display:flex;gap:12px;font-size:12px;margin-top:16px;align-items:center}
.stats .sep{opacity:.5}
.walk{font-size:11.5px;opacity:.85;margin-top:8px;display:flex;gap:6px;align-items:center}
.hero-ctas{display:flex;gap:14px;margin-top:30px}
.hero-rating{display:flex;align-items:center;gap:10px;font-size:10.5px;margin-top:38px;padding-top:18px;border-top:1px solid rgba(255,255,255,.18);width:964px}
.stars{color:var(--gold);letter-spacing:2px}
.hero-rating strong{font-family:"Fraunces",serif;font-size:15px}
.chev{position:absolute;left:50%;bottom:22px;transform:translateX(-50%)}

/* TRUST BAR */
.trust{height:106px;background:var(--sand);border-bottom:1px solid var(--line)}
.trust .wrap{display:flex;justify-content:space-between;align-items:center;height:100%;padding:0 20px}
.trust-item{display:flex;align-items:center;gap:12px;width:210px}
.trust-icon{width:32px;height:32px;border-radius:50%;background:#ebdccb;display:flex;align-items:center;justify-content:center;flex:none}
.trust-item b{display:block;font-size:11px;font-weight:600}
.trust-item span{font-size:9.5px;color:var(--muted)}

/* WELCOME */
.welcome{height:631px;padding-top:86px}
.welcome .wrap{display:flex;justify-content:space-between}
.welcome-text{width:450px}
.welcome-text h2{font-size:36px}
.welcome-text h2 em{color:var(--rust);font-style:italic;font-weight:600}
.welcome-text p{font-size:13px;color:#4b443c;margin-top:18px;line-height:1.78}
.welcome-text p + p{margin-top:14px}
.hosts{display:flex;align-items:center;gap:14px;margin-top:22px;font-size:10.5px}
.monogram{width:36px;height:36px;border-radius:50%;background:#eadcc8;display:flex;align-items:center;justify-content:center;font-family:"Fraunces",serif;font-size:12px;font-weight:600;color:#7a5a3b}
.hosts b{font-weight:600;display:block}
.hosts span{color:var(--muted)}
.collage{width:490px;height:420px;position:relative}
.collage .main{position:absolute;left:35px;top:18px;width:450px;height:338px;background:linear-gradient(160deg,#5b84b8 0%,#8eaa7a 50%,#6f8a55 100%);box-shadow:0 18px 40px rgba(60,40,20,.18)}
.collage .inset{position:absolute;left:0;top:156px;width:186px;height:227px;background:linear-gradient(170deg,#7aa0c9 0%,#8c8a5a 50%,#7a6a4a 100%);border:5px solid #fff;box-shadow:0 12px 26px rgba(60,40,20,.22)}
.badge-min{position:absolute;right:0;top:0;width:140px;height:62px;background:var(--forest);color:#fff;border-radius:10px;padding:10px 16px}
.badge-min b{font-family:"Fraunces",serif;font-size:19px;font-weight:500;display:block;line-height:1.1}
.badge-min span{font-size:7.5px;letter-spacing:.2em}

/* HOUSE */
.house{height:712px;background:var(--sand);padding-top:90px}
.section-head{display:flex;justify-content:space-between;align-items:flex-end}
.section-head p{font-size:13px;color:#4b443c;margin-top:18px;width:520px}
.rooms{display:flex;gap:16px;margin-top:48px}
.room{width:229px;height:287px}
.room::after{content:"";position:absolute;inset:0;background:linear-gradient(180deg,rgba(0,0,0,0) 55%,rgba(25,18,12,.6) 100%)}
.room-label{position:absolute;left:16px;bottom:16px;z-index:1;color:#fff}
.room-label b{font-family:"Fraunces",serif;font-size:14px;font-weight:500;display:block}
.room-label span{font-size:8px;letter-spacing:.2em;opacity:.85;display:block;margin-top:2px}
.amenities{display:flex;justify-content:center;gap:32px;margin-top:34px;font-size:10.5px;color:#4b443c}
.amenities span{display:flex;gap:6px;align-items:center}
.amenities i{width:5px;height:5px;border-radius:50%;background:#c9b49a;display:inline-block}

/* LOCATION */
.location{height:677px;padding-top:88px}
.location .wrap{display:flex;justify-content:space-between}
.loc-text{width:425px}
.loc-text > p{font-size:13px;color:#4b443c;margin-top:18px}
.distances{margin-top:22px;list-style:none}
.distances li{display:flex;justify-content:space-between;align-items:center;height:45.5px;border-bottom:1px solid var(--line);font-size:11.5px}
.tag{background:#ece2d4;border-radius:9px;padding:2px 8px;font-size:7.5px;letter-spacing:.12em;font-weight:600;color:#6c5c48}
.loc-text .link-arrow{display:inline-block;margin-top:30px}
.map-card{width:488px;height:346px;border-radius:12px;background:#fff;box-shadow:0 14px 34px rgba(60,40,20,.12);overflow:hidden}
.map-area{height:300px;background:linear-gradient(135deg,#e7e1d6 0%,#ddd7c8 40%,#cfd9d2 70%,#e2dccf 100%)}
.map-foot{height:46px;display:flex;justify-content:space-between;align-items:center;padding:0 20px;font-size:10px;color:var(--muted)}
.map-foot span{display:flex;gap:6px;align-items:center}
.map-foot a{color:var(--rust);font-weight:600;text-decoration:none}

/* REVIEWS */
.reviews{height:606px;background:var(--sand);padding-top:90px}
.review-cards{display:flex;gap:14px;margin-top:44px}
.review{width:312px;height:224px;background:var(--cream);border-radius:12px;padding:22px 22px;box-shadow:0 4px 14px rgba(60,40,20,.05)}
.review .stars{font-size:11px}
.review p{font-size:11px;line-height:1.75;color:#4b443c;margin-top:10px;height:98px}
.review .who{border-top:1px solid var(--line);margin-top:12px;padding-top:12px;font-size:10.5px}
.review .who b{font-weight:600}
.review .who span{color:var(--muted)}
.review .who small{display:block;font-size:8.5px;color:var(--muted)}

/* BOOK DIRECT */
.book{height:523px;position:relative;color:var(--on-dark);text-align:center}
.book-photo{position:absolute;inset:0;background:linear-gradient(120deg,#3a4b35 0%,#33432f 50%,#2f3e2b 100%)}
.book-inner{position:relative;padding-top:88px}
.book h2{font-family:"Fraunces",serif;font-weight:500;font-size:38px;line-height:1.2;margin-top:14px}
.book h2 em{display:block;font-style:normal;color:#d77a4b}
.book p{font-size:13px;line-height:1.8;width:470px;margin:22px auto 0;opacity:.88}
.book-ctas{display:flex;justify-content:center;align-items:center;gap:18px;margin-top:30px}
.call{font-family:"Fraunces",serif;font-size:15px;color:#fff;border-bottom:1px solid rgba(255,255,255,.6)}
.fine{font-size:8.5px;letter-spacing:.2em;opacity:.55;margin-top:34px}

/* FOOTER */
.footer{height:343px;background:var(--forest-deep);color:var(--on-dark);padding-top:56px}
.foot-cols{display:flex}
.foot-brand{width:299px}
.foot-brand .brand{font-size:19px}
.foot-brand p{font-size:10px;line-height:1.8;opacity:.8;margin-top:16px;width:270px}
.foot-meta{font-size:8.5px;opacity:.7;margin-top:14px;line-height:1.8}
.foot-col{width:222px;font-size:10.5px}
.foot-col h4{font-size:8px;letter-spacing:.25em;font-weight:600;opacity:.65;margin-bottom:12px}
.foot-col li{list-style:none;line-height:2.3;opacity:.9}
.foot-col .btn{margin-top:14px;height:38px;font-size:10px}
.foot-bottom{display:flex;justify-content:space-between;margin-top:36px;padding-top:16px;border-top:1px solid rgba(255,255,255,.12);font-size:8.5px;opacity:.6}
.foot-bottom span{margin-left:20px}
</style>
</head>
<body>

<header class="hero">
  <div class="hero-photo" role="img" aria-label="Living room with stone fireplace, cream sofas and large windows"></div>
  <div class="wrap">
    <nav class="nav">
      <div class="brand">Birch Lantern Retreat<small>BEND · OREGON</small></div>
      <div class="nav-links"><span>The House</span><span>Gallery</span><span>Explore Bend</span><span>Reviews</span><span>Book Direct</span></div>
      <div class="nav-right">
        <span>
          <svg width="10" height="10" viewBox="0 0 24 24" fill="none" stroke="#fff" stroke-width="2"><path d="M5 3h4l2 5-3 2a11 11 0 0 0 6 6l2-3 5 2v4a2 2 0 0 1-2 2A17 17 0 0 1 3 5a2 2 0 0 1 2-2z"/></svg>
          (541) 555-0192
        </span>
        <a class="btn btn-rust">Book Direct →</a>
      </div>
    </nav>
    <div class="hero-content">
      <span class="pill">● BEND, OREGON · TANNERY ROW QUARTER</span>
      <h1>Birch Lantern Retreat</h1>
      <div class="tagline">Your Bend, Oregon getaway</div>
      <div class="stats"><span>3 Bedrooms</span><span class="sep">|</span><span>2 Baths</span><span class="sep">|</span><span>Sleeps 6</span><span class="sep">|</span><span>♥ Pet Friendly</span></div>
      <div class="walk">
        <svg width="10" height="10" viewBox="0 0 24 24" fill="none" stroke="#d77a4b" stroke-width="2.5"><circle cx="12" cy="12" r="9"/><circle cx="12" cy="12" r="3"/></svg>
        Walk to Bend's Tannery Row Quarter — about five minutes, coffee in hand
      </div>
      <div class="hero-ctas">
        <a class="btn btn-rust">Book Direct →</a>
        <a class="btn btn-ghost">Check Availability</a>
      </div>
      <div class="hero-rating">
        <span class="stars">★★★★★</span><strong>4.98</strong><span>Guest Rating · 200+ Reviews</span>
        <span style="opacity:.4">|</span>
        <span>◎ Staynest Visitor Pick · Top 1% of Eligible Homes</span>
      </div>
    </div>
  </div>
  <svg class="chev" width="14" height="14" viewBox="0 0 24 24" fill="none" stroke="#fff" stroke-width="2"><path d="M6 9l6 6 6-6"/></svg>
</header>

<section class="trust">
  <div class="wrap">
    <div class="trust-item"><div class="trust-icon"><svg width="14" height="14" viewBox="0 0 24 24" fill="none" stroke="#b65a30" stroke-width="2"><path d="M12 3l2.7 5.6 6.1.9-4.4 4.3 1 6.1L12 17l-5.4 2.9 1-6.1-4.4-4.3 6.1-.9z"/></svg></div><div><b>4.98★ Guest Rating</b><span>across 205 reviews</span></div></div>
    <div class="trust-item"><div class="trust-icon"><svg width="14" height="14" viewBox="0 0 24 24" fill="none" stroke="#b65a30" stroke-width="2"><path d="M12 20s-7-4.4-7-10a4 4 0 0 1 7-2.5A4 4 0 0 1 19 10c0 5.6-7 10-7 10z"/></svg></div><div><b>Staynest Visitor Pick</b><span>since 2022</span></div></div>
    <div class="trust-item"><div class="trust-icon"><svg width="14" height="14" viewBox="0 0 24 24" fill="none" stroke="#b65a30" stroke-width="2"><path d="M3 17l6-6 4 4 8-8M15 7h6v6"/></svg></div><div><b>Top 1% of Homes</b><span>on Staynest, of eligible listings</span></div></div>
    <div class="trust-item"><div class="trust-icon"><svg width="14" height="14" viewBox="0 0 24 24" fill="none" stroke="#b65a30" stroke-width="2"><circle cx="12" cy="9" r="5"/><path d="M9 13l-1 8 4-2 4 2-1-8"/></svg></div><div><b>Prime Keeper</b><span>every year we've hosted</span></div></div>
  </div>
</section>

<section class="welcome">
  <div class="wrap">
    <div class="welcome-text">
      <div class="eyebrow">Welcome</div>
      <h2 class="section-title">A beautiful Bend home<br>where you can <em>actually relax.</em></h2>
      <p>Birch Lantern Retreat is that rare vacation home that feels designed rather than assembled: a stone fireplace that draws a crowd, a kitchen you'll actually cook in, and a fenced backyard where the day ends around the fire pit. It's comfortable luxury — the kind you notice in the first five minutes and stop noticing by the second morning, because it just feels like home.</p>
      <p>The location does the rest. Bend's Tannery Row Quarter — river trail, shops, dinner, concerts at Larkspur Fields Pavilion — is a five-minute walk. Downtown, the breweries and the Cascades are minutes by car. Bring the dog. Bring the kids. Bring nothing but the coffee order you'll walk to.</p>
      <div class="hosts">
        <div class="monogram">D&amp;O</div>
        <div><b>Dana &amp; Owen — your hosts</b><span>Managing Birch Lantern Retreat since 2019</span></div>
        <div style="margin-left:14px"><span class="stars" style="font-size:10px">★</span> 4.98 from 205 guest reviews</div>
      </div>
    </div>
    <div class="collage">
      <div class="photo main" role="img" aria-label="Front of the gray craftsman house with green lawn and pine trees"></div>
      <div class="photo inset" role="img" aria-label="Fenced backyard with a tree and stone landscaping"></div>
      <div class="badge-min"><b>5 min</b><span>WALK TO TANNERY ROW</span></div>
    </div>
  </div>
</section>

<section class="house">
  <div class="wrap">
    <div class="eyebrow">The House</div>
    <div class="section-head">
      <div>
        <h2 class="section-title">Designed for slow<br>mornings and full days</h2>
        <p>Three real bedrooms, two full baths and every comfort considered — walk through the whole house.</p>
      </div>
      <a class="link-arrow">Explore the house →</a>
    </div>
    <div class="rooms">
      <div class="photo room" role="img" aria-label="Living room with sectional sofa and tufted ottoman" style="background:linear-gradient(160deg,#c9bfb1,#8f7f6d)"><div class="room-label"><b>The Living Room</b><span>STONE FIREPLACE · WOOD STOVE</span></div></div>
      <div class="photo room" role="img" aria-label="Kitchen with white cabinets, granite island and dining table" style="background:linear-gradient(160deg,#d6d0c6,#7f6a55)"><div class="room-label"><b>The Kitchen</b><span>GRANITE ISLAND · GAS RANGE</span></div></div>
      <div class="photo room" role="img" aria-label="Primary bedroom with king bed and chandelier" style="background:linear-gradient(160deg,#d9d2c6,#9c8c78)"><div class="room-label"><b>Primary Suite</b><span>KING BED · EN-SUITE</span></div></div>
      <div class="photo room" role="img" aria-label="Fenced backyard patio with fire pit and pines" style="background:linear-gradient(160deg,#7e94a4,#5d5a48)"><div class="room-label"><b>The Backyard</b><span>FENCED · FIRE PIT · DOGS<br>WELCOME</span></div></div>
    </div>
    <div class="amenities">
      <span><i></i>Stone fireplace</span><span><i></i>Fast WiFi</span><span><i></i>Washer &amp; dryer</span><span><i></i>Fenced yard</span><span><i></i>Free parking</span><span><i></i>A/C + heat</span>
    </div>
  </div>
</section>

<section class="location">
  <div class="wrap">
    <div class="loc-text">
      <div class="eyebrow">The Location</div>
      <h2 class="section-title">The neighborhood<br>is the amenity</h2>
      <p>Guests tell us the walkability changes the whole shape of the trip: park the car on arrival, and mostly forget it.</p>
      <ul class="distances">
        <li>Tannery Row Quarter — shops, dining, river trail<span class="tag">5 MIN WALK</span></li>
        <li>Deschutes River Trail access<span class="tag">4 MIN WALK</span></li>
        <li>Larkspur Fields Pavilion<span class="tag">9 MIN WALK</span></li>
        <li>Downtown Bend &amp; Drake Park<span class="tag">8 MIN DRIVE</span></li>
        <li>Bend Hop Trail breweries<span class="tag">5 MIN DRIVE</span></li>
        <li>Pine Crest Summit &amp; Cascade Lakes<span class="tag">35 MIN DRIVE</span></li>
      </ul>
      <a class="link-arrow">Explore Bend, the local's way →</a>
    </div>
    <div class="map-card">
      <div class="map-area" role="img" aria-label="Street map of Bend showing the house near Tannery Row Quarter"></div>
      <div class="map-foot">
        <span><svg width="10" height="10" viewBox="0 0 24 24" fill="none" stroke="#b65a30" stroke-width="2.5"><path d="M12 21s-7-6.5-7-12a7 7 0 0 1 14 0c0 5.5-7 12-7 12z"/><circle cx="12" cy="9" r="2.5"/></svg>Near SE Alder Ln &amp; Ridge St · Bend's Tannery Row Quarter</span>
        <a>Open in maps</a>
      </div>
    </div>
  </div>
</section>

<section class="reviews">
  <div class="wrap">
    <div class="eyebrow">Guest Reviews</div>
    <div class="section-head">
      <div>
        <h2 class="section-title">4.98 stars. 200+ stays.<br>The receipts.</h2>
        <p>Staynest Visitor Pick, Prime Keeper every year, top 1% of eligible homes — here's what that sounds like.</p>
      </div>
      <a class="link-arrow">Read all reviews →</a>
    </div>
    <div class="review-cards">
      <div class="review"><div class="stars">★★★★★</div><p>“We've stayed in a lot of Bend rentals and this one is on another level. The location is genuinely unbeatable — we walked to the Tannery Row Quarter for dinner both nights and never moved the car until we left for… ”</p><div class="who"><b>Lena K.</b> <span>· August 2026</span><small>Family of five · 4 nights</small></div></div>
      <div class="review"><div class="stars">★★★★★</div><p>“Booked because it was pet friendly; would rebook for the backyard alone. Our golden had the time of his life, and the fenced yard meant zero worry. The fire pit at night with the high-desert sky is something we… ”</p><div class="who"><b>Marcus &amp; Ivy T.</b> <span>· July 2026</span><small>Couple + golden retriever · 3 nights</small></div></div>
      <div class="review"><div class="stars">★★★★★</div><p>“Two families of three and the house fit us perfectly — everyone had their own real bedroom (not a converted closet), and the living room meant the kids had space while the grown-ups got the patio. The hosts' gu… ”</p><div class="who"><b>The Calloways</b> <span>· June 2026</span><small>Two families · 6 nights</small></div></div>
    </div>
  </div>
</section>

<section class="book">
  <div class="book-photo" role="img" aria-label="Dim evening view of the backyard patio with fire pit"></div>
  <div class="book-inner">
    <div class="eyebrow">Book Direct</div>
    <h2>Stay at Birch Lantern Retreat.<em>Book direct, skip the fees.</em></h2>
    <p>The same home, the same calendar synced with Staynest &amp; Hoplo — without the 12–15% platform service fee on top. Real availability, complete pricing, instant confirmation.</p>
    <div class="book-ctas"><a class="btn btn-rust">Check Availability →</a><span class="call">or call (541) 555-0192</span></div>
    <div class="fine">FREE CANCELLATION UP TO 30 DAYS · SECURE PAYMENT · INSTANT CONFIRMATION</div>
  </div>
</section>

<footer class="footer">
  <div class="wrap">
    <div class="foot-cols">
      <div class="foot-brand">
        <div class="brand">Birch Lantern Retreat<small>BEND · OREGON</small></div>
        <p>A warm, professionally managed vacation home a five-minute walk from the Tannery Row Quarter — for slow mornings, river afternoons and fireside evenings.</p>
        <div class="foot-meta"><span class="stars">★</span> 4.98 · 205 reviews &nbsp;·&nbsp; Prime Keeper &nbsp;·<br>Visitor Pick</div>
      </div>
      <div class="foot-col"><h4>EXPLORE</h4><ul><li>Home</li><li>The House</li><li>Gallery</li><li>Explore Bend</li><li>Reviews</li><li>Book Direct</li><li>Contact &amp; FAQ</li></ul></div>
      <div class="foot-col"><h4>THE STAY</h4><ul><li>3 bedrooms · 2 baths · sleeps 6</li><li>Pet friendly (2 dogs)</li><li>Check-in 4 PM · check-out 10 AM</li><li>Free driveway parking</li><li>Fast WiFi</li></ul></div>
      <div class="foot-col"><h4>BOOK &amp; CONTACT</h4><ul><li>☏ (541) 555-0192</li><li>stay@birchlanternretreat.com</li><li style="line-height:1.6;margin-top:6px;opacity:.7">Near SE Alder Ln &amp; Ridge St ·<br>Bend's Tannery Row Quarter</li></ul><a class="btn btn-rust">Check Availability →</a></div>
    </div>
    <div class="foot-bottom">
      <div>© 2026 Birch Lantern Retreat · Bend, Oregon. All rights reserved.</div>
      <div><span>House rules</span><span>Cancellation policy</span><span>Calendar synced with Staynest &amp; Hoplo</span></div>
    </div>
  </div>
</footer>

</body>
</html>
```